Equipment Finance Specialist I work with companies who need the funds to buy their equipment

I would like a business card that stands out on the shelves. I want to be able to hand it to someone and say WOW. This card should have my logo.
You can put color into it I am very open on design and color

What my company does is we deal with dealerships that sell equipment such as Dump Trucks garbage trucks tractors trailers. Customers get referred to us and depending on their time in business we will ask for the following items

Companies that have been in business for more than two years we have a credit application program up to 250K . With this program we need the following items Credit application filled out(which is what I would like to be able for the customer to click on my website to get.) as well as three current month bank statements.

Deals over 250k we will need the following items

2 years business tax returns
2 years personal tax returns
Profit & Loss statement
Personal Financial Statement

what we do
100% FINANCING
SEASONAL PAYMENTS
LOAN BALLOON PAYMENTS
TRAC LEASING
LOW-INTEREST REFINANCING RATES
DEBT CONSOLIDATION

We specialize in creative financing solutions and offer a variety of reliable, flexible and expandable lending choices.

Target Market(s)

Trucking Companies

Industry/Entity Type

Trucking Company

Contact Information for Business Card

* $250,000 Application only Program
* Loans from $30,000 to 5,000,000
* Competitive Interest Rates

Font styles to use
Serif
Sans Serif

Colors

Designer to choose colors to be used in the design.

Requirements
Must have
• On the back of the card.
• * $250,000 Application only Program
• * Loans from $30,000 to 5,000,000
• My name, email, website. address
• * Competitive Interest Rates
• * 100% Financing
Nice to have
• I want my logo to pop on the card
• My logo is the great one I would like to use
Should not have
• I am up for your creativity as well

```html
<!DOCTYPE html>
<html lang="en">
<head>
<meta charset="utf-8">
<title>Ridgeway Capital — Business Card</title>
<link href="https://fonts.googleapis.com/css2?family=Montserrat:wght@400;500;600;700;800&display=swap" rel="stylesheet">
<style>
  :root {
    --navy: #1d2d6b;
    --navy-light: #2c3f85;
    --red: #e0202e;
    --white: #ffffff;
    --stage: #2a2a2c;
  }
  * { margin: 0; padding: 0; box-sizing: border-box; }
  html, body {
    width: 1200px; height: 930px; overflow: hidden;
    background: var(--stage);
    font-family: "Montserrat", Arial, sans-serif;
  }
  .canvas { position: relative; width: 1200px; height: 930px; }
  .card {
    position: absolute;
    width: 540px; height: 310px;
    border-radius: 18px;
    overflow: hidden;
    box-shadow: 0 18px 40px rgba(0,0,0,0.45);
  }
  .card--front {
    left: 90px; top: 110px;
    background: linear-gradient(120deg, var(--navy) 0%, var(--navy-light) 55%, var(--navy) 100%);
    display: flex; align-items: center; justify-content: center;
  }
  .card--back { left: 570px; top: 510px; background: var(--navy); }
  .card__shape { position: absolute; inset: 0; }

  .brand { display: flex; align-items: center; gap: 14px; }
  .brand__dot {
    width: 58px; height: 58px; border-radius: 50%;
    border: 6px solid currentColor;
  }
  .brand__name {
    font-weight: 800; text-transform: uppercase;
    line-height: 1; letter-spacing: 1px;
  }
  .card--front .brand { color: var(--white); }
  .card--front .brand__name { font-size: 40px; }
  .card--back .brand {
    position: absolute; right: 34px; top: 40px; color: var(--navy);
  }
  .card--back .brand__dot { width: 42px; height: 42px; border-width: 5px; }
  .card--back .brand__name { font-size: 26px; }

  .contact {
    position: absolute; left: 34px; bottom: 24px;
    color: var(--white); font-size: 13px; line-height: 1.45;
  }
  .contact__name {
    color: var(--red); font-size: 22px; font-weight: 500;
    text-transform: uppercase; line-height: 1.1;
  }
  .contact__role { font-size: 14px; margin-bottom: 10px; }
  .contact__address { margin-bottom: 8px; }
  .contact__line { display: flex; align-items: center; gap: 8px; }
  .contact__icon { width: 12px; height: 12px; flex: none; }
  .contact__web { font-weight: 700; }

  .offers {
    position: absolute; right: 30px; bottom: 24px;
    list-style: none; color: var(--white);
    font-size: 12px; font-weight: 600; line-height: 1.6;
    text-align: right;
  }
  .offers__item::before {
    content: ""; display: inline-block;
    width: 6px; height: 6px; margin-right: 8px;
    background: var(--red); border-radius: 50%;
    vertical-align: middle;
  }
</style>
</head>
<body>
<main class="canvas">

  <section class="card card--front" aria-label="Card front">
    <div class="brand">
      <span class="brand__dot"></span>
      <span class="brand__name">Ridgeway<br>Capital</span>
    </div>
  </section>

  <section class="card card--back" aria-label="Card back">
    <svg class="card__shape" viewBox="0 0 540 310" preserveAspectRatio="none" aria-hidden="true">
      <path d="M170 0 Q250 200 540 200 L540 0 Z" fill="var(--white)"/>
      <path d="M170 0 Q250 200 540 200" fill="none" stroke="var(--red)" stroke-width="5"/>
      <path d="M162 0 Q244 212 540 212" fill="none" stroke="var(--white)" stroke-width="2" opacity="0.5"/>
    </svg>

    <div class="brand">
      <span class="brand__dot"></span>
      <span class="brand__name">Ridgeway<br>Capital</span>
    </div>

    <div class="contact">
      <p class="contact__name">Daniel Carter</p>
      <p class="contact__role">Director</p>
      <p class="contact__address">4120 Maple Ridge Dr.<br>Austin, TX 78701</p>
      <p class="contact__line">
        <svg class="contact__icon" viewBox="0 0 12 12"><path d="M2 1 L4.5 1 L5.5 3.5 L4 4.6 Q5 7 7.4 8 L8.5 6.5 L11 7.5 L11 10 Q6 11 2.5 7.5 Q0.8 5 2 1 Z" fill="var(--red)"/></svg>
        1300 472 615
      </p>
      <p class="contact__line">
        <svg class="contact__icon" viewBox="0 0 12 12"><rect x="1" y="2.5" width="10" height="7" fill="none" stroke="var(--red)" stroke-width="1.3"/><path d="M1 2.5 L6 6.5 L11 2.5" fill="none" stroke="var(--red)" stroke-width="1.3"/></svg>
        info@ridgewaycapital.com
      </p>
      <p class="contact__line contact__web">
        <svg class="contact__icon" viewBox="0 0 12 12"><circle cx="6" cy="6" r="5" fill="none" stroke="var(--red)" stroke-width="1.2"/><ellipse cx="6" cy="6" rx="2.2" ry="5" fill="none" stroke="var(--red)" stroke-width="1"/><path d="M1 6 H11" stroke="var(--red)" stroke-width="1"/></svg>
        www.ridgewaycapital.com
      </p>
    </div>

    <ul class="offers">
      <li class="offers__item">$250,000 Application Only Program</li>
      <li class="offers__item">Loans from $30,000 to $5,000,000</li>
      <li class="offers__item">Competitive Interest Rates</li>
      <li class="offers__item">100% Financing</li>
    </ul>
  </section>

</main>
</body>
</html>
```